Business Card for Professional Photographer

I'm looking for an eye catching modern clean design that compliments my logo/ website fonts & colours.
I specialise in architecture, corporate & commercial photography so I'm marketing to professional clients rather than portrait / wedding clients.

I would prefer to not have a solid black design.

My logo brand guide is as follows :

Main front font. : Reislust
Main font colour : #fff
Slogan front font : Ubuntu Bold
Monogram front font : Venti Medium
Container colour : #fff

I need print ready files in pdf .png & .eps formats.

Included in the files below are some screen grabs as reference to font & colours etc.

```html
<!DOCTYPE html>
<html lang="en">
<head>
<meta charset="UTF-8">
<title>Lumen Line – Business Card</title>
<link rel="stylesheet" href="https://fonts.googleapis.com/css2?family=Roboto:wght@400&family=Barlow+Semi+Condensed:wght@600&family=Ubuntu:wght@400&display=swap">
<style>
  :root {
    --bg: #b9b9b9;
    --gold-deep: #bf9650;
    --gold-mid: #d2b46e;
    --gold-light: #e9db98;
    --ink: #1b1b1b;
    --ink-soft: #2a2a2a;
    --paper: #f1f1f1;
    --gold-text: #a9823c;
  }
  * { margin: 0; padding: 0; box-sizing: border-box; }
  html, body { width: 1200px; height: 576px; overflow: hidden; }
  body { background: var(--bg); position: relative; }

  .card {
    position: absolute;
    top: 139px;
    height: 293px;
    border-radius: 11px;
    overflow: hidden;
    box-shadow: 0 3px 8px rgba(0,0,0,.25);
  }

  /* Shared wordmark: plain name beside a plain square */
  .wordmark {
    position: absolute;
    display: flex;
    align-items: center;
    justify-content: center;
    gap: 10px;
    font-family: "Roboto", sans-serif;
    font-weight: 400;
    white-space: nowrap;
  }
  .wordmark__square { display: block; flex: none; }

  /* Front */
  .card--front {
    left: 81px;
    width: 485px;
    background: linear-gradient(60deg, var(--gold-deep) 0%, var(--gold-mid) 45%, var(--gold-light) 100%);
  }
  .card--front .wordmark { left: 0; right: 0; top: 118px; font-size: 30px; color: var(--ink); }
  .card--front .wordmark__square { width: 14px; height: 14px; background: var(--ink); }
  .card--front .website {
    position: absolute;
    left: 0; right: 0; top: 256px;
    text-align: center;
    font-family: "Ubuntu", sans-serif;
    font-size: 12.5px;
    letter-spacing: 2px;
    color: var(--ink-soft);
  }

  /* Back */
  .card--back { left: 602px; width: 481px; background: var(--paper); }
  .card--back .panel { position: absolute; inset: 0; }
  .person { position: absolute; left: 27px; top: 27px; color: var(--ink); }
  .person__name { font-family: "Barlow Semi Condensed", sans-serif; font-weight: 600; font-size: 20px; line-height: 1.1; }
  .person__role { font-family: "Roboto", sans-serif; font-size: 12.5px; margin-top: 4px; }
  .contact { position: absolute; left: 27px; top: 181px; list-style: none; font-family: "Roboto", sans-serif; font-size: 12.5px; color: var(--ink); }
  .contact li { display: flex; align-items: center; height: 18.5px; }
  .contact svg { width: 11px; height: 11px; margin-right: 13px; fill: var(--ink); }
  .address { position: absolute; left: 27px; top: 240px; font-family: "Roboto", sans-serif; font-size: 12.5px; color: var(--ink); }
  .card--back .wordmark { left: 280px; width: 162px; top: 132px; font-size: 21px; color: var(--gold-text); }
  .card--back .wordmark__square { width: 10px; height: 10px; background: var(--gold-text); }
</style>
</head>
<body>

<section class="card card--front">
  <div class="wordmark">
    <span class="wordmark__square"></span>
    <span class="wordmark__name">Lumen Line</span>
  </div>
  <div class="website">www.lumenline.com.au</div>
</section>

<section class="card card--back">
  <svg class="panel" viewBox="0 0 481 293" preserveAspectRatio="none" aria-hidden="true">
    <defs>
      <linearGradient id="backGold" x1="0" y1="0" x2="1" y2="0.3">
        <stop offset="0" stop-color="#bf9650"/>
        <stop offset="0.6" stop-color="#d0b16a"/>
        <stop offset="1" stop-color="#e4cf88"/>
      </linearGradient>
    </defs>
    <path d="M0 0 H278 C248 70 242 200 282 293 H0 Z" fill="#f0dc8a"/>
    <path d="M0 0 H270 C240 70 234 200 274 293 H0 Z" fill="url(#backGold)"/>
  </svg>

  <div class="person">
    <div class="person__name">Marcus Hale</div>
    <div class="person__role">Photographer</div>
  </div>

  <ul class="contact">
    <li><svg viewBox="0 0 12 12"><path d="M1 4c0-2 2-3 5-3s5 1 5 3v1H8V4H4v1H1zM3 6h6l2 5H1z"/></svg>0412555018</li>
    <li><svg viewBox="0 0 12 12"><path d="M0 2h12v8H0zM1 3v.4l5 3.4 5-3.4V3z"/></svg>info@lumenline.com.au</li>
    <li><svg viewBox="0 0 12 12"><circle cx="6" cy="6" r="5.5" fill="none" stroke="#1b1b1b" stroke-width="1"/><path d="M0.5 6h11M6 .5c-3 3-3 8 0 11M6 .5c3 3 3 8 0 11" fill="none" stroke="#1b1b1b" stroke-width="0.9"/></svg>www.lumenline.com.au</li>
  </ul>
  <div class="address">48 Harbour Rd Portfield Vic 3199</div>

  <div class="wordmark">
    <span class="wordmark__square"></span>
    <span class="wordmark__name">Lumen Line</span>
  </div>
</section>

</body>
</html>
```